VOMRA Pty Ltd Business Card

Looking for a simple yet eye-catching double-sided business card design using my company logo on one side and contact details on the other.

Target Market(s)

Government

Industry/Entity Type

Communication Systems Engineering

Contact Information for Business Card

VOMRA Pty Ltd

Requirements
Nice to have
• Would be great to have a QR code so details can be scanned into contacts

```html
<!DOCTYPE html>
<html lang="en">
<head>
<meta charset="utf-8">
<title>VOMRA Pty Ltd Business Card</title>
<link rel="stylesheet" href="https://fonts.googleapis.com/css2?family=Open+Sans:wght@400;700&display=swap">
<style>
  :root {
    --backdrop: #232323;
    --card-light: #ffffff;
    --card-dark: #37424a;
    --ink-dark: #37424a;
    --ink-light: #ffffff;
    --corner: 130px;
  }
  * { box-sizing: border-box; margin: 0; padding: 0; }
  html, body {
    width: 1200px; height: 780px; overflow: hidden;
    background: var(--backdrop);
    font-family: "Open Sans", Arial, sans-serif;
  }
  .card-set {
    position: absolute; inset: 0;
    display: flex; justify-content: center; align-items: center; gap: 80px;
  }
  .card {
    position: relative;
    width: 360px; height: 590px;
    overflow: hidden;
  }
  .card-front {
    background: var(--card-light);
    border-radius: var(--corner) 0 var(--corner) 0;
  }
  .card-back {
    background: var(--card-dark);
    border-radius: 0 var(--corner) 0 var(--corner);
    color: var(--ink-light);
  }
  .front-mark {
    position: absolute; left: 50%; top: 295px;
    transform: translate(-50%, -50%) rotate(-90deg);
    display: flex; align-items: center; gap: 30px;
    white-space: nowrap;
  }
  .front-mark .wordmark {
    font-weight: 700; font-size: 72px; letter-spacing: 4px;
    color: var(--ink-dark); line-height: 1;
  }
  .front-mark .mark-dot {
    flex: none;
    width: 96px; height: 96px; border-radius: 50%;
    background: var(--ink-dark);
  }
  .back-brand {
    position: absolute; top: 70px; left: 0; right: 0;
    display: flex; justify-content: center; align-items: center; gap: 16px;
  }
  .back-brand .mark-dot {
    width: 44px; height: 44px; border-radius: 50%; background: var(--ink-light);
  }
  .back-brand .wordmark {
    font-weight: 700; font-size: 46px; letter-spacing: 3px; line-height: 1;
  }
  .contact {
    position: absolute; left: 0; right: 0; top: 300px;
    text-align: center;
  }
  .person-name { font-weight: 700; font-size: 26px; line-height: 1.1; }
  .person-role { font-size: 15px; margin-top: 2px; }
  .icon-row {
    display: flex; justify-content: center; gap: 8px; margin: 16px 0 8px;
  }
  .icon {
    width: 28px; height: 28px; border-radius: 50%;
    background: var(--ink-light);
    display: flex; align-items: center; justify-content: center;
  }
  .icon svg { width: 16px; height: 16px; }
  .details { font-size: 16px; line-height: 1.35; }
  .address-icon { margin: 18px auto 10px; }
  .address { font-size: 16px; line-height: 1.35; }
</style>
</head>
<body>
<main class="card-set">
  <section class="card card-front" aria-label="Card front">
    <div class="front-mark">
      <span class="mark-dot"></span>
      <span class="wordmark">VOMRA</span>
    </div>
  </section>

  <section class="card card-back" aria-label="Card back">
    <div class="back-brand">
      <span class="mark-dot"></span>
      <span class="wordmark">VOMRA</span>
    </div>
    <div class="contact">
      <p class="person-name">Daniel Hartley</p>
      <p class="person-role">Co-Founder</p>
      <div class="icon-row">
        <span class="icon"><svg viewBox="0 0 16 16"><path d="M4 2l2.5 2.5-1.5 1.5c.8 1.8 2.2 3.2 4 4l1.5-1.5L13 11l-1.5 2.5C7 13 3 9 2.5 4.5z" fill="#37424a"/></svg></span>
        <span class="icon"><svg viewBox="0 0 16 16"><rect x="2" y="4" width="12" height="8" rx="1" fill="none" stroke="#37424a" stroke-width="1.6"/><path d="M2.5 4.5L8 9l5.5-4.5" fill="none" stroke="#37424a" stroke-width="1.6"/></svg></span>
        <span class="icon"><svg viewBox="0 0 16 16"><circle cx="8" cy="8" r="5.5" fill="none" stroke="#37424a" stroke-width="1.6"/><ellipse cx="8" cy="8" rx="2.3" ry="5.5" fill="none" stroke="#37424a" stroke-width="1.3"/><path d="M2.5 8h11" stroke="#37424a" stroke-width="1.3"/></svg></span>
      </div>
      <p class="details">(555) 014-3382<br>www.vomra.com.au<br>admin@vomra.com.au</p>
      <span class="icon address-icon"><svg viewBox="0 0 16 16"><path d="M8 1.5a4.5 4.5 0 0 0-4.5 4.5c0 3.3 4.5 8.5 4.5 8.5s4.5-5.2 4.5-8.5A4.5 4.5 0 0 0 8 1.5z" fill="#37424a"/><circle cx="8" cy="6" r="1.7" fill="#fff"/></svg></span>
      <p class="address">47-49 Harlow Street Westmere<br>NSW 2150 Australia</p>
    </div>
  </section>
</main>
</body>
</html>
```